Marlowe Group needs a business card

I would like the card to be simple but modern and elegant.
I like black and white.
or black and gold.
we are a private finance lender and also are involved in property and property developments.

please look at the business card photos i provided i would like M.G only one one side and all the other details on the other side use fonts that tie in with my theme.

Industry/Entity Type

Finance

Contact Information for Business Card

Marlowe Group (M.G) Daniel Marlowe M: 0413586207 E: danmarl@inboxmail.test

Font styles to use
Other font styles liked:
• Use fonts that would reflect our business

Colors
000000
ffffff

Requirements
Must have
• one side of details
• other side has either M.G or Marlowe Group like in the photos provided

```html
<!DOCTYPE html>
<html lang="en">
<head>
<meta charset="utf-8">
<title>Marlowe Group – Business Card</title>
<link rel="stylesheet" href="https://fonts.googleapis.com/css2?family=Cinzel:wght@400;600&family=Open+Sans:wght@400;700&display=swap">
<style>
  :root {
    --backdrop: #ababab;
    --card-black: #000000;
    --gold: #f2c224;
    --white: #ffffff;
    --faint-line: #262626;
  }
  html, body {
    margin: 0;
    padding: 0;
    width: 1200px;
    height: 900px;
    overflow: hidden;
    background: var(--backdrop);
  }
  .stage {
    position: relative;
    width: 1200px;
    height: 900px;
  }
  .card {
    position: absolute;
    top: 215px;
    width: 414px;
    height: 414px;
    border-radius: 50%;
    background: var(--card-black);
    overflow: hidden;
  }
  .card--front { left: 164px; }
  .card--back { left: 623px; }

  .brand-square {
    position: absolute;
    left: 126px;
    top: 125px;
    width: 150px;
    height: 118px;
    display: block;
  }
  .brand-name {
    position: absolute;
    left: 0;
    right: 0;
    top: 266px;
    margin: 0;
    text-align: center;
    font-family: "Cinzel", serif;
    font-weight: 400;
    font-size: 23px;
    letter-spacing: 0.5px;
    color: var(--gold);
  }

  .back-frame {
    position: absolute;
    left: 60px;
    top: 85px;
    width: 292px;
    height: 246px;
    display: block;
  }
  .holder-name {
    position: absolute;
    left: 0;
    right: 0;
    top: 122px;
    margin: 0;
    text-align: center;
    font-family: "Cinzel", serif;
    font-weight: 600;
    font-size: 29px;
    letter-spacing: 0.5px;
    color: var(--gold);
  }
  .contact {
    position: absolute;
    left: 0;
    right: 0;
    top: 232px;
    margin: 0;
    text-align: center;
    font-family: "Open Sans", sans-serif;
    font-size: 20px;
    line-height: 28px;
    color: var(--white);
  }
  .contact__label {
    color: var(--gold);
    font-weight: 700;
  }
  .contact__line { display: block; }
</style>
</head>
<body>
  <main class="stage">
    <section class="card card--front" aria-label="Card front">
      <svg class="brand-square" viewBox="0 0 150 118" aria-hidden="true">
        <rect x="3" y="3" width="144" height="112" fill="none" stroke="var(--gold)" stroke-width="5"/>
      </svg>
      <p class="brand-name">Marlowe Group</p>
    </section>

    <section class="card card--back" aria-label="Card back">
      <svg class="back-frame" viewBox="0 0 292 246" aria-hidden="true">
        <rect x="3" y="3" width="286" height="240" fill="none" stroke="var(--faint-line)" stroke-width="5"/>
      </svg>
      <h1 class="holder-name">Daniel Marlowe</h1>
      <p class="contact">
        <span class="contact__line"><span class="contact__label">M:</span> 0413586207</span>
        <span class="contact__line"><span class="contact__label">E:</span> danmarl@inboxmail.test</span>
      </p>
    </section>
  </main>
</body>
</html>
```